New business card for a regional office of a US M&A company

We need business card for a finance company, office based in Hong Kong , our Head office is in US, our business is to Merge and acquires companies , the new office will be a regional office for the Asia Pacific region. We want to use the head office logo as attached ( but don't have to be exactly the same, can be a variation to it) as a base and then add Asia Pacific alongside the logo.
We would prefer to have be bilingual Eng + Chinese, although we don't really have Chinese company name .

Industry/Entity Type

Business

Contact Information for Business Card

Clara Jo Tsang
 

VP,
APAC M&A Operations
Orin Vantage Asia Pacific Limited
 
Unit 1407, K18
18 Tai Lok Shan Road, 
Hong Kong 
 
M: +852 6038 1742
T : +852 2836 4100
F : +852 2836 4177
VOIP: 4158
 
cjtsang@orinvantage.com

Font styles to use
Serif
Sans Serif

Colors

Designer to choose colors to be used in the design.

Requirements
Must have
• APAC Office

```html
<!DOCTYPE html>
<html lang="en">
<head>
<meta charset="utf-8">
<title>Orin Vantage — Business Card</title>
<link href="https://fonts.googleapis.com/css2?family=Open+Sans:wght@400;600;700;800&family=Oswald:wght@500;600&display=swap" rel="stylesheet">
<style>
  :root {
    --navy: #0c2340;
    --navy-deep: #0a1a33;
    --cyan: #1fa9c9;
    --ink: #2b2b2b;
    --grey: #555a5f;
    --paper: #ffffff;
    --backdrop: #e6e7e9;
  }
  * { margin: 0; padding: 0; box-sizing: border-box; }
  html, body { width: 1200px; height: 900px; overflow: hidden; }
  body {
    background: var(--backdrop);
    font-family: "Open Sans", Arial, sans-serif;
    display: flex;
    flex-direction: column;
    align-items: center;
    justify-content: center;
    gap: 48px;
  }
  .card {
    width: 630px;
    height: 360px;
    position: relative;
    box-shadow: 0 6px 18px rgba(0,0,0,0.18);
  }

  /* Front */
  .card--front {
    background: linear-gradient(160deg, var(--navy) 0%, var(--navy-deep) 100%);
    display: flex;
    flex-direction: column;
    align-items: center;
    justify-content: center;
    gap: 22px;
  }
  .brand-square {
    width: 76px; height: 76px;
    background: var(--paper);
  }
  .brand-name--front {
    color: var(--cyan);
    font-weight: 800;
    font-size: 50px;
    letter-spacing: 3px;
    line-height: 1;
  }

  /* Back */
  .card--back { background: var(--paper); }
  .identity {
    position: absolute;
    left: 64px; top: 118px;
    width: 262px;
    text-align: right;
  }
  .person-name {
    font-family: "Oswald", "Arial Narrow", sans-serif;
    font-weight: 600;
    font-size: 36px;
    color: var(--cyan);
    line-height: 1.05;
    text-transform: uppercase;
    letter-spacing: 0.3px;
    text-align: left;
  }
  .person-role {
    font-size: 16px;
    color: var(--ink);
    line-height: 1.3;
    margin-top: 4px;
  }
  .divider {
    position: absolute;
    left: 342px; top: 112px;
    width: 3px; height: 86px;
    background: var(--cyan);
  }
  .contacts {
    position: absolute;
    left: 368px; top: 114px;
    list-style: none;
  }
  .contacts li {
    display: flex;
    align-items: center;
    gap: 12px;
    font-size: 16px;
    color: var(--grey);
    line-height: 21px;
    letter-spacing: 0.5px;
  }
  .contacts svg { width: 13px; height: 13px; flex: none; }
  .footer {
    position: absolute;
    left: 48px; bottom: 38px;
    display: flex;
    align-items: flex-end;
    gap: 14px;
  }
  .footer-brand {
    display: flex;
    flex-direction: column;
    align-items: center;
    gap: 5px;
  }
  .brand-square--small {
    width: 20px; height: 20px;
    background: var(--navy);
  }
  .brand-name--small {
    color: var(--cyan);
    font-weight: 800;
    font-size: 12px;
    letter-spacing: 0.5px;
  }
  .footer-rule {
    width: 2px; height: 16px;
    background: var(--cyan);
  }
  .address {
    color: var(--cyan);
    font-size: 17px;
    letter-spacing: 0.4px;
    line-height: 1;
  }
</style>
</head>
<body>
  <section class="card card--front" aria-label="Card front">
    <div class="brand-square" aria-hidden="true"></div>
    <div class="brand-name--front">ORIN VANTAGE</div>
  </section>

  <section class="card card--back" aria-label="Card back">
    <div class="identity">
      <h1 class="person-name">Clara Jo Tsang</h1>
      <p class="person-role">VP,<br>APAC M&amp;A Operations</p>
    </div>
    <div class="divider"></div>
    <ul class="contacts">
      <li>
        <svg viewBox="0 0 14 14" aria-label="Mobile"><rect x="4" y="1" width="6" height="12" rx="1" fill="none" stroke="#1fa9c9" stroke-width="1.4"/></svg>
        +852 6038 1742
      </li>
      <li>
        <svg viewBox="0 0 14 14" aria-label="Telephone"><path d="M3 2 L5 2 L6 5 L4.5 6 Q6 9 8 9.5 L9 8 L12 9 L12 11 Q12 12.5 10.5 12.5 Q2 11 1.5 3.5 Q1.5 2 3 2Z" fill="#1fa9c9"/></svg>
        +852 2836 4100
      </li>
      <li>
        <svg viewBox="0 0 14 14" aria-label="Fax"><rect x="4" y="1.5" width="6" height="3" fill="#1fa9c9"/><rect x="1.5" y="5" width="11" height="5.5" rx="1" fill="#1fa9c9"/><rect x="4" y="9" width="6" height="3.5" fill="#fff" stroke="#1fa9c9" stroke-width="1"/></svg>
        +852 2836 4177
      </li>
      <li>
        <svg viewBox="0 0 14 14" aria-label="Email"><rect x="1" y="3" width="12" height="8.5" fill="#1fa9c9"/><path d="M1 3 L7 8 L13 3" fill="none" stroke="#fff" stroke-width="1.2"/></svg>
        cjtsang@orinvantage.com
      </li>
    </ul>
    <div class="footer">
      <div class="footer-brand">
        <div class="brand-square--small" aria-hidden="true"></div>
        <span class="brand-name--small">ORIN VANTAGE</span>
      </div>
      <div class="footer-rule"></div>
      <p class="address">Unit 1407, K18 18 Tai Lok Shan Road, Hong Kong</p>
    </div>
  </section>
</body>
</html>
```